Seeking funky, innovative business cards

I am looking to refresh our current business cards to something more engaging, visual and impactful. We are a management consultancy firm, see website (www.larkstone-partners.com.au). I've included our colour scheme, sample of the slides we use and our old business cards. We would like our cards to have icons. The card should display:- Name- Title- Mobile number- Address- Email address- Website - Company logo- Our purpose statement "We create the best places on earth to work"

Contact Information for Business Card

Brennan Ulfsson
Consultant
0468 927 341
Level 3, 218 Wexley Street, Melbourne 3000
brennan@larkstone-partners.com.au
www.larkstone-partners.com.au

Purpose statement "we create the best places on earth to work"
LOGO available in google images

Font styles to use
Other font styles liked:
• Open Sans Light, Bebas Neue (open to other cool foints)

Colors
ffc214
5c5c5c
f5f5f5
fefefe

Requirements
Must have
• - Name
• - Title
• - Mobile number
• - Address
• - Email address
• - Website
• - Company logo
• - Our purpose statement "We create the best places on earth to work"
Nice to have
• - Icons
• - Colour (see our colour scheme"

```html
<!DOCTYPE html>
<html lang="en">
<head>
<meta charset="utf-8">
<title>Larkstone Partners – Business Card</title>
<link rel="stylesheet" href="https://fonts.googleapis.com/css2?family=Bebas+Neue&family=Open+Sans:wght@300;400;600;700&display=swap">
<style>
  :root {
    --brand-yellow: #ffc214;
    --band-yellow: #fec547;
    --ink-grey: #5c5c5c;
    --ink-dark: #3a3a3a;
    --paper: #fefefe;
    --backdrop: #e4e4e4;
    --icon-white: #fefefe;
    --band-height: 278px;
  }
  * { box-sizing: border-box; margin: 0; padding: 0; }
  html, body {
    width: 1200px;
    height: 800px;
    overflow: hidden;
    background: var(--backdrop);
    font-family: "Open Sans", Arial, sans-serif;
  }
  .stage {
    position: relative;
    width: 1200px;
    height: 800px;
    display: flex;
    align-items: center;
    justify-content: center;
    gap: 70px;
  }
  .card {
    position: relative;
    width: 340px;
    height: 525px;
    background: var(--paper);
    box-shadow: 0 10px 28px rgba(0,0,0,0.14);
    overflow: hidden;
  }

  /* Front side */
  .card-front {
    display: flex;
    align-items: center;
    justify-content: center;
  }
  .wordmark {
    display: flex;
    align-items: center;
    gap: 12px;
  }
  .wordmark-dot {
    width: 14px;
    height: 14px;
    border-radius: 50%;
    background: var(--brand-yellow);
  }
  .wordmark-name {
    font-family: "Open Sans", Arial, sans-serif;
    font-weight: 300;
    font-size: 30px;
    letter-spacing: 0.5px;
    color: var(--ink-grey);
  }

  /* Back side */
  .purpose {
    position: absolute;
    top: 48px;
    left: 38px;
    font-family: "Bebas Neue", Impact, sans-serif;
    font-size: 22px;
    line-height: 0.98;
    color: var(--brand-yellow);
    text-transform: uppercase;
  }
  .purpose span { display: block; }
  .identity {
    position: absolute;
    left: 38px;
    bottom: calc(var(--band-height) + 8px);
  }
  .identity-name {
    font-weight: 700;
    font-size: 19px;
    line-height: 1.2;
    color: var(--ink-grey);
    letter-spacing: 0.3px;
  }
  .identity-title {
    font-weight: 400;
    font-size: 13px;
    line-height: 1.25;
    color: var(--ink-dark);
    margin-top: 1px;
  }
  .contact-band {
    position: absolute;
    left: 0;
    right: 0;
    bottom: 0;
    height: var(--band-height);
    background: var(--band-yellow);
    padding: 34px 20px 0 38px;
  }
  .contact-list { list-style: none; }
  .contact-item {
    display: flex;
    align-items: flex-start;
    gap: 16px;
    margin-bottom: 14px;
    font-size: 13px;
    line-height: 1.3;
    color: var(--ink-dark);
  }
  .contact-icon {
    flex: 0 0 20px;
    width: 20px;
    height: 20px;
  }
  .contact-text { padding-top: 1px; }
</style>
</head>
<body>
<main class="stage">

  <section class="card card-front" aria-label="Business card front">
    <div class="wordmark">
      <span class="wordmark-dot"></span>
      <span class="wordmark-name">Larkstone Partners</span>
    </div>
  </section>

  <section class="card card-back" aria-label="Business card back">
    <p class="purpose">
      <span>We create</span>
      <span>the best places</span>
      <span>on earth to work.</span>
    </p>

    <div class="identity">
      <p class="identity-name">Brennan Ulfsson</p>
      <p class="identity-title">Consultant</p>
    </div>

    <div class="contact-band">
      <ul class="contact-list">
        <li class="contact-item">
          <svg class="contact-icon" viewBox="0 0 20 20" aria-hidden="true">
            <path d="M10 1.5a6 6 0 0 0-6 6c0 4.5 6 11 6 11s6-6.5 6-11a6 6 0 0 0-6-6z" fill="var(--icon-white)"/>
            <circle cx="10" cy="7.5" r="2.3" fill="var(--band-yellow)"/>
          </svg>
          <span class="contact-text">Level 3, 218 Wexley Street<br>Melbourne 3000</span>
        </li>
        <li class="contact-item">
          <svg class="contact-icon" viewBox="0 0 20 20" aria-hidden="true">
            <path d="M4.5 2.5l3 0.5 1.2 3.6-2 1.6a10 10 0 0 0 5 5l1.6-2 3.6 1.2 0.5 3c-0.2 1-1 1.6-2 1.6C8.6 17 3 11.4 2.9 4.5c0-1 0.6-1.8 1.6-2z" fill="var(--icon-white)"/>
          </svg>
          <span class="contact-text">0468 927 341</span>
        </li>
        <li class="contact-item">
          <svg class="contact-icon" viewBox="0 0 20 20" aria-hidden="true">
            <rect x="1.5" y="4" width="17" height="12" fill="none" stroke="var(--icon-white)" stroke-width="1.8"/>
            <path d="M1.5 4l8.5 7 8.5-7M1.5 16l6-5.5M18.5 16l-6-5.5" fill="none" stroke="var(--icon-white)" stroke-width="1.6"/>
          </svg>
          <span class="contact-text">brennan@larkstone-partners.com.au</span>
        </li>
        <li class="contact-item">
          <svg class="contact-icon" viewBox="0 0 20 20" aria-hidden="true">
            <circle cx="10" cy="10" r="8.5" fill="var(--icon-white)"/>
            <g fill="none" stroke="var(--band-yellow)" stroke-width="1.1">
              <ellipse cx="10" cy="10" rx="3.6" ry="8.5"/>
              <path d="M1.5 10h17M3 5.8h14M3 14.2h14M10 1.5v17"/>
            </g>
          </svg>
          <span class="contact-text">www.larkstone-partners.com.au</span>
        </li>
      </ul>
    </div>
  </section>

</main>
</body>
</html>
```